Create a memorable Stationary for Security Software Company

Velbrantix is the worldwide leader in securing the Internet. Making Internet communications and critical data secure, reliable and available everywhere has been and continues to be our ongoing vision. We are committed to staying focused on real customer needs and to developing new and innovative security solutions that redefine the security landscape.

Industry/Entity Type

Internet

Font styles to use
Serif
Sans Serif
Script

Colors
0792cd
33a6d7
85cae6

```html
<!DOCTYPE html>
<html lang="en">
<head>
<meta charset="utf-8">
<title>Velbrantix Business Card</title>
<link href="https://fonts.googleapis.com/css2?family=Open+Sans:wght@400;600;700&display=swap" rel="stylesheet">
<style>
  :root {
    --brand-deep: #0792cd;
    --brand-mid: #33a6d7;
    --brand-light: #85cae6;
    --card-front: #80c8e8;
    --ink: #3a3a3a;
    --ink-soft: #555555;
    --paper: #ffffff;
    --backdrop: #ecedef;
  }
  * { margin: 0; padding: 0; box-sizing: border-box; }
  html, body {
    width: 1200px; height: 1120px; overflow: hidden;
    background: var(--backdrop);
    font-family: "Open Sans", sans-serif;
  }
  .sheet { position: relative; width: 1200px; height: 1120px; }
  .card {
    position: absolute; left: 220px; width: 760px; height: 434px;
    overflow: hidden;
    box-shadow: 0 6px 18px rgba(0,0,0,0.18);
  }
  .card--front { top: 70px; background: var(--card-front); }
  .card--back { top: 600px; background: var(--paper); }

  .brand {
    display: flex; align-items: center; gap: 14px;
    color: var(--brand-deep); font-weight: 700; white-space: nowrap;
  }
  .brand__dot { border-radius: 50%; background: var(--brand-mid); flex: none; }
  .card--front .brand {
    position: absolute; top: 150px; left: 0; right: 0; justify-content: center;
    font-size: 52px; color: #1f88c0;
  }
  .card--front .brand__dot { width: 54px; height: 54px; background: #3fa0d4; }
  .front__url {
    position: absolute; top: 318px; left: 0; right: 0; text-align: center;
    font-size: 21px; letter-spacing: 4px; color: var(--ink);
  }

  .identity { position: absolute; top: 80px; left: 0; display: flex; align-items: flex-start; }
  .identity__tab {
    width: 22px; height: 62px; background: var(--brand-deep);
    border-radius: 0 14px 14px 0; margin-right: 22px;
  }
  .identity__name { font-size: 25px; font-weight: 700; color: var(--brand-deep); line-height: 1.2; }
  .identity__title { font-size: 20px; color: var(--ink-soft); line-height: 1.4; }

  .card--back .brand { position: absolute; top: 76px; right: 60px; font-size: 38px; }
  .card--back .brand__dot { width: 40px; height: 40px; }

  .contacts {
    position: absolute; left: 66px; top: 236px; list-style: none;
    font-size: 19px; color: var(--ink);
  }
  .contacts li { display: flex; align-items: center; gap: 10px; height: 30px; white-space: nowrap; }
  .contacts li:last-child { margin-top: 8px; }
  .contacts svg { width: 17px; height: 17px; fill: var(--brand-deep); flex: none; }

  .web-band {
    position: absolute; right: 0; bottom: 28px; width: 320px; height: 44px;
    background: var(--brand-deep); border-radius: 22px 0 0 22px;
    color: var(--paper); font-size: 19px; letter-spacing: 1.5px;
    display: flex; align-items: center; justify-content: center; white-space: nowrap;
  }
</style>
</head>
<body>
<main class="sheet">
  <section class="card card--front">
    <div class="brand"><span class="brand__dot"></span><span>Velbrantix</span></div>
    <p class="front__url">www.velbrantix.com</p>
  </section>

  <section class="card card--back">
    <div class="identity">
      <span class="identity__tab"></span>
      <div>
        <p class="identity__name">Your Name</p>
        <p class="identity__title">Title</p>
      </div>
    </div>

    <div class="brand"><span class="brand__dot"></span><span>Velbrantix</span></div>

    <ul class="contacts">
      <li>
        <svg viewBox="0 0 24 24" aria-hidden="true"><path d="M6.6 10.8a15 15 0 0 0 6.6 6.6l2.2-2.2c.3-.3.7-.4 1-.2 1.1.4 2.3.6 3.6.6.6 0 1 .4 1 1V20c0 .6-.4 1-1 1A17 17 0 0 1 3 4c0-.6.4-1 1-1h3.5c.6 0 1 .4 1 1 0 1.3.2 2.5.6 3.6.1.3 0 .7-.2 1z"/></svg>
        012-345-6789
      </li>
      <li>
        <svg viewBox="0 0 24 24" aria-hidden="true"><path d="M8 1h8a2 2 0 0 1 2 2v18a2 2 0 0 1-2 2H8a2 2 0 0 1-2-2V3a2 2 0 0 1 2-2zm0 3v13h8V4zm4 15a1.2 1.2 0 1 0 0 2.4 1.2 1.2 0 0 0 0-2.4z"/></svg>
        012-345-6789
      </li>
      <li>
        <svg viewBox="0 0 24 24" aria-hidden="true"><path d="M2 6h20v12H2zm2 2v.4l8 5 8-5V8l-8 5z"/></svg>
        info@velbrantix.com
      </li>
      <li>
        <svg viewBox="0 0 24 24" aria-hidden="true"><path d="M12 1a8 8 0 0 0-8 8c0 6 8 14 8 14s8-8 8-14a8 8 0 0 0-8-8zm0 11a3 3 0 1 1 0-6 3 3 0 0 1 0 6z"/></svg>
        Street Name, City Name, Zipcode-012345
      </li>
    </ul>

    <div class="web-band">www.velbrantix.com</div>
  </section>
</main>
</body>
</html>
```